Real Estate Business Card

On the front side I want to have my info, my brokerage info.
On the back side I want have my complany’s logo, website and Facebook link. I will provide all this once I select a design.

I would like to see Black background and gold text, Dark Blue and gold text and White and blue text designs

Font styles to use
Sans Serif
Script

```html
<!DOCTYPE html>
<html lang="en">
<head>
<meta charset="utf-8">
<title>Harbor Key Realty – Business Card</title>
<link href="https://fonts.googleapis.com/css2?family=Cinzel:wght@500;600&family=Open+Sans:wght@400;600&display=swap" rel="stylesheet">
<style>
  :root {
    --stage: #3a3a3c;
    --blue-light: #2d5fc4;
    --blue-dark: #1a3d8f;
    --blue-ink: #1f4fae;
    --gold: #e9bd3c;
    --white: #ffffff;
    --text-grey: #4a4a4a;
    --rule: #e3e3e3;
  }
  * { box-sizing: border-box; margin: 0; padding: 0; }
  html, body { width: 1200px; height: 782px; overflow: hidden; }
  body {
    background: var(--stage);
    display: flex;
    align-items: center;
    justify-content: center;
    gap: 40px;
    font-family: "Open Sans", sans-serif;
  }
  .card {
    position: relative;
    width: 560px;
    height: 320px;
    overflow: hidden;
    box-shadow: 0 10px 28px rgba(0,0,0,0.45);
  }

  /* Back side */
  .card--back {
    background: linear-gradient(180deg, var(--blue-light) 0%, var(--blue-dark) 100%);
    display: flex;
    flex-direction: column;
    align-items: center;
    justify-content: center;
  }
  .brand-name {
    font-family: "Cinzel", serif;
    font-weight: 600;
    letter-spacing: 1px;
    white-space: nowrap;
  }
  .card--back .brand-name {
    color: var(--gold);
    font-size: 40px;
  }
  .web-link {
    margin-top: 30px;
    color: var(--white);
    font-size: 13px;
    letter-spacing: 0.5px;
  }

  /* Front side */
  .card--front { background: var(--white); }
  .card--front .brand-name {
    position: absolute;
    top: 112px;
    left: 262px;
    color: var(--blue-ink);
    font-size: 25px;
  }
  .person {
    position: absolute;
    top: 46px;
    left: 34px;
  }
  .person__name {
    font-family: "Cinzel", serif;
    font-weight: 600;
    color: var(--blue-ink);
    font-size: 19px;
    letter-spacing: 0.5px;
  }
  .person__title {
    color: var(--text-grey);
    font-size: 13px;
    margin-bottom: 6px;
  }
  .contact-list { list-style: none; }
  .contact-list li {
    display: flex;
    align-items: center;
    gap: 7px;
    color: var(--text-grey);
    font-size: 13.5px;
    line-height: 20px;
  }
  .contact-list svg { width: 11px; height: 11px; fill: var(--blue-ink); flex: none; }
  .divider {
    position: absolute;
    left: 262px;
    right: 34px;
    top: 186px;
    height: 1px;
    background: var(--rule);
  }
  .address {
    position: absolute;
    right: 40px;
    bottom: 42px;
    text-align: right;
    color: #2b2b2b;
    font-size: 14px;
    line-height: 20px;
  }
  .band {
    position: absolute;
    left: 0; right: 0; bottom: 0;
    height: 10px;
    background: var(--blue-ink);
  }
</style>
</head>
<body>

  <section class="card card--front" aria-label="Business card front">
    <div class="person">
      <p class="person__name">Dorian Hale</p>
      <p class="person__title">Managing Director</p>
      <ul class="contact-list">
        <li><svg viewBox="0 0 12 12" aria-hidden="true"><path d="M2.5 0.5l2 2-1 1.5c.7 1.6 1.9 2.8 3.5 3.5l1.5-1 2 2-1.2 1.7C5 10 2 7 .8 1.7z"/></svg>044-555 210 347</li>
        <li><svg viewBox="0 0 12 12" aria-hidden="true"><path d="M3 0h6a1 1 0 0 1 1 1v10a1 1 0 0 1-1 1H3a1 1 0 0 1-1-1V1a1 1 0 0 1 1-1zm0.5 1.5v8h5v-8z"/></svg>044-555 210 348</li>
        <li><svg viewBox="0 0 12 12" aria-hidden="true"><path d="M0 2h12v8H0zM1 3l5 3.5L11 3v-.2H1z"/></svg>info@harborkeyrealty.com</li>
        <li><svg viewBox="0 0 12 12" aria-hidden="true"><circle cx="6" cy="6" r="6"/></svg>www.harborkeyrealty.com</li>
      </ul>
    </div>
    <p class="brand-name">Harbor Key Realty</p>
    <div class="divider"></div>
    <p class="address">48 Quayside Lane,<br>Port Ellis, 20419</p>
    <div class="band"></div>
  </section>

  <section class="card card--back" aria-label="Business card back">
    <p class="brand-name">Harbor Key Realty</p>
    <p class="web-link">WWW.HARBORKEYREALTY.COM/COMMUNITY</p>
  </section>

</body>
</html>
```